Harbourline Electrical Solutions

On one side. LOGO (underneath:) Commercial Industrial Residential

- NAME & CONTACT DETAILS

Marcus T. Hollings
Project Manager

(Cell icon) (441) 555-0187
(Email icon) hlelectricalsolutions@mailvento.com
(Facebook & Instagram icons )@hlelectricalsolutions

Other side: LOGO - underneath ELECTRICAL CONSTRUCTION & MAINTENANCE . LED LIGHTING & AUTOMATION . LIFE SAFETY SYSTEMS (FIRE ALARM / SECURITY) . DATA & COMMUNICATION

```html
<!DOCTYPE html>
<html lang="en">
<head>
<meta charset="utf-8">
<title>Harbourline Electrical Solutions — Business Card</title>
<link rel="stylesheet" href="https://fonts.googleapis.com/css2?family=Montserrat:wght@400;500;600;700&display=swap">
<style>
  :root {
    --teal: #0f566b;
    --white: #ffffff;
    --ink: #2b2b2b;
    --muted: #3a3a3a;
    --backdrop: #e9eaec;
  }
  * { box-sizing: border-box; margin: 0; padding: 0; }
  html, body {
    width: 1200px; height: 1200px; overflow: hidden;
    background: var(--backdrop);
    font-family: "Montserrat", Arial, sans-serif;
  }
  .sheet {
    width: 1200px; height: 1200px;
    display: flex; flex-direction: column; align-items: center; justify-content: center;
    gap: 48px;
  }
  .card {
    position: relative;
    width: 880px; height: 528px;
    box-shadow: 0 10px 30px rgba(0,0,0,0.18);
    overflow: hidden;
  }
  /* Front */
  .card--front { background: var(--teal); color: var(--white); }
  .services {
    position: absolute; left: 73px; top: 220px;
    list-style: none;
    font-weight: 600; font-size: 16.5px; line-height: 26.5px;
    letter-spacing: 0.01em;
  }
  .services li::before {
    content: ""; display: inline-block;
    width: 6px; height: 6px; border-radius: 50%;
    background: var(--white);
    margin-right: 9px; vertical-align: middle; position: relative; top: -2px;
  }
  .wordmark-vertical {
    position: absolute; right: 79px; bottom: 310px;
    writing-mode: vertical-rl; transform: rotate(180deg);
    font-weight: 500; font-size: 20px; line-height: 27px;
    letter-spacing: 0.14em; color: var(--white);
  }
  .wordmark-vertical .words { display: flex; flex-direction: column-reverse; }
  .wordmark-rule {
    position: absolute; left: 703px; top: 241px;
    width: 120px; height: 2px; background: var(--white);
  }
  /* Back */
  .card--back { background: var(--white); }
  .brand {
    position: absolute; left: 91px; top: 214px;
  }
  .brand__name {
    display: flex; align-items: center; gap: 14px;
    color: var(--teal); font-weight: 600;
    font-size: 20px; line-height: 23px; letter-spacing: 0.14em;
  }
  .brand__square { width: 16px; height: 16px; background: var(--teal); flex: none; }
  .brand__tagline {
    margin-top: 22px; white-space: nowrap;
    font-weight: 500; font-size: 10px; letter-spacing: 0.17em; color: var(--muted);
  }
  .brand__tagline .sep { color: var(--teal); margin: 0 3px; }
  .divider {
    position: absolute; left: 434px; top: 192px;
    width: 2px; height: 144px; background: var(--teal);
  }
  .contact { position: absolute; left: 455px; top: 190px; }
  .contact__name {
    color: var(--teal); font-weight: 700; font-size: 25px; letter-spacing: 0.01em;
  }
  .contact__role { color: var(--ink); font-weight: 500; font-size: 16.5px; margin-top: 1px; }
  .contact__list { list-style: none; margin-top: 18px; }
  .contact__list li {
    display: flex; align-items: center; gap: 5px;
    color: var(--ink); font-weight: 400; font-size: 18px; line-height: 28px;
    letter-spacing: 0.02em;
  }
  .icon { width: 18px; height: 18px; flex: none; }
  .icon--gap { margin-right: 4px; }
</style>
</head>
<body>
<main class="sheet">
  <section class="card card--front" aria-label="Card front">
    <ul class="services">
      <li>ELECTRICAL CONSTRUCTION &amp; MAINTENANCE</li>
      <li>LED LIGHTING &amp; AUTOMATION</li>
      <li>LIFE SAFETY SYSTEMS (FIRE ALARM / SECURITY)</li>
      <li>DATA &amp; COMMUNICATION</li>
    </ul>
    <div class="wordmark-vertical">
      <div class="words">
        <span>SOLUTIONS</span>
        <span>ELECTRICAL</span>
        <span>HARBOURLINE</span>
      </div>
    </div>
    <div class="wordmark-rule"></div>
  </section>

  <section class="card card--back" aria-label="Card back">
    <div class="brand">
      <div class="brand__name">
        <span class="brand__square"></span>
        <span>HARBOURLINE<br>ELECTRICAL<br>SOLUTIONS</span>
      </div>
      <p class="brand__tagline">COMMERCIAL<span class="sep">|</span>INDUSTRIAL<span class="sep">|</span>RESIDENTIAL</p>
    </div>
    <div class="divider"></div>
    <div class="contact">
      <h1 class="contact__name">MARCUS T. HOLLINGS</h1>
      <p class="contact__role">Project Manager</p>
      <ul class="contact__list">
        <li>
          <svg class="icon" viewBox="0 0 20 20" aria-hidden="true">
            <circle cx="10" cy="10" r="9" fill="none" stroke="#0f566b" stroke-width="1.4"/>
            <path d="M7 5.5l1.6 2.4-1 1c.6 1.4 1.6 2.4 3 3l1-1 2.4 1.6-.9 1.6c-3.6-.3-6.4-3.1-6.7-6.7z" fill="#0f566b"/>
          </svg>
          (441) 555-0187
        </li>
        <li>
          <svg class="icon" viewBox="0 0 20 20" aria-hidden="true">
            <circle cx="10" cy="10" r="9" fill="none" stroke="#0f566b" stroke-width="1.4"/>
            <rect x="5.5" y="7" width="9" height="6.5" fill="none" stroke="#0f566b" stroke-width="1.2"/>
            <path d="M5.5 7l4.5 3.5L14.5 7" fill="none" stroke="#0f566b" stroke-width="1.2"/>
          </svg>
          hlelectricalsolutions@mailvento.com
        </li>
        <li>
          <svg class="icon" viewBox="0 0 20 20" aria-hidden="true">
            <circle cx="10" cy="10" r="9" fill="none" stroke="#0f566b" stroke-width="1.4"/>
            <path d="M8.6 11.4l2.8-2.8M9.2 7.6l1-1a2 2 0 0 1 2.8 2.8l-1 1M10.8 12.4l-1 1a2 2 0 0 1-2.8-2.8l1-1" fill="none" stroke="#0f566b" stroke-width="1.3" stroke-linecap="round"/>
          </svg>
          <svg class="icon icon--gap" viewBox="0 0 20 20" aria-hidden="true">
            <circle cx="10" cy="10" r="9" fill="none" stroke="#0f566b" stroke-width="1.4"/>
            <path d="M5.8 6.5h8.4v5.6H9.5l-2.5 2v-2H5.8z" fill="none" stroke="#0f566b" stroke-width="1.2" stroke-linejoin="round"/>
          </svg>
          @hlelectricalsolutions
        </li>
      </ul>
    </div>
  </section>
</main>
</body>
</html>
```